Hi,
We are also sourcing for a logo, if you have ideas please take a look at our other project (if you look at our profile you should be able to see it).
We are looking for a website that will be used to manage mobile devices. The feature set is rather small, users can Wipe, Lock, Locate devices as well as make them Ring or Speak (by sending text to be spoken). We attached some images of what it looks like right now. We are looking for simplicity, uniformity and most importantly, the website should be thought of as primary User Interface, it should flow.
Please see attached to get an idea of what it looks like now. The current design was inspired by making a site that will work and flow well on a variety of displays (from mobile to tablet to desktop).
We want to stay away from radio buttons, check-boxes. This should be engaging and creative, opposite of Corporate. Not busy (ideally we are looking to have fewest possible choices at any given time and at the same time no feature should be more than 3 clicks away (this is a suggestion/approximation... just want to share our understanding of what 'flow' is).
Could be cartoony.
Thanks!
BrisketLoom
Reason: there are a couple of designs that are interesting, in addition to specific feedback I provided, possibly looking for more concepts.
Thank You

```html
<!DOCTYPE html>
<html lang="en">
<head>
<meta charset="utf-8">
<title>BrisketLoom – Lost Your Phone?</title>
<link rel="stylesheet" href="https://fonts.googleapis.com/css2?family=Federo&family=Kalam:wght@400&family=Open+Sans:wght@400;600;700&display=swap">
<style>
  :root{
    --topbar:#62a6cc;
    --header:#5a9cc4;
    --header-dark:#4f8db4;
    --accent:#4f9ac6;
    --paper:#f4f5f5;
    --ink:#333;
    --muted:#777;
    --rule:#c9cbcc;
    --footer:#333333;
    --footer-text:#d8d8d8;
    --field:#f1f1f1;
  }
  *{box-sizing:border-box;margin:0;padding:0}
  html,body{width:1075px;height:1200px;overflow:hidden}
  body{position:relative;background:var(--paper);font-family:"Open Sans",Arial,sans-serif;color:var(--ink)}
  h1,h2,h3{font-weight:400}
  .abs{position:absolute}

  .topbar{left:0;top:0;width:1075px;height:65px;background:var(--topbar);border-bottom:2px solid #3f7ea5}
  .util-nav{left:90px;top:32px;display:flex;gap:22px;font-size:12px;color:#fff}
  .search{left:811px;top:31px;width:170px;height:25px;background:var(--header-dark);color:#fff;font-size:13px;padding:4px 10px}
  .search svg{position:absolute;right:-22px;top:-4px}

  .header{left:0;top:65px;width:1075px;height:83px;background:var(--header);box-shadow:0 8px 12px rgba(0,0,0,.18)}
  .brand{left:92px;top:22px;font-family:"Federo",sans-serif;font-size:31px;color:#fff}
  .main-nav{left:424px;top:25px;display:flex;font-family:"Federo",sans-serif;font-variant:small-caps;font-size:17px;color:#fff}
  .main-nav span{padding:3px 11px;margin-right:20px}
  .main-nav .current{background:var(--header-dark);border:1px solid #437fa6}

  .hero-title{left:0;width:1075px;top:190px;text-align:center;font-family:"Federo",sans-serif;font-size:37px;color:var(--accent)}
  .features{top:285px;left:0;width:1075px}
  .feature{position:absolute;display:flex;align-items:center;gap:12px;font-family:"Kalam",cursive;font-size:27px;color:#333}
  .rule{height:2px;background:linear-gradient(90deg,transparent,var(--rule) 15%,var(--rule) 85%,transparent)}

  .cta{left:383px;top:381px;width:318px;height:74px;border-radius:37px;background:linear-gradient(#c4c4c4,#a6a6a6);border:3px solid #b5b5b5;box-shadow:0 2px 4px rgba(0,0,0,.25)}
  .cta svg{position:absolute;left:6px;top:4px}
  .cta span{position:absolute;left:92px;top:14px;font-family:"Federo",sans-serif;font-size:32px;color:#fff}

  .section-title{font-family:"Federo",sans-serif;font-size:22px;color:#222}
  .body-copy{font-size:10.5px;line-height:15.2px;color:var(--muted);text-align:justify}
  .photo{border:3px solid #cfd0d0;box-shadow:0 1px 3px rgba(0,0,0,.2)}
  .card-title{font-family:Georgia,serif;font-weight:bold !important;font-size:14px;color:var(--accent)}

  .news-item .news-title{display:flex;align-items:center;gap:6px;font-weight:600;font-size:13px;color:#444;margin-left:-21px}
  .news-item .body-copy{margin-top:8px}

  .footer{left:0;top:967px;width:1075px;height:233px;background:var(--footer)}
  .footer-head{font-size:13px;font-weight:600;color:#fff}
  .btn{background:linear-gradient(#f3f3f3,#cfcfcf);border:1px solid #999;border-radius:3px;color:#222;font-size:9.5px;text-align:center}
  .blog-copy{font-size:9.2px;line-height:13.5px;color:var(--footer-text);text-align:justify;width:240px}
  .blog-sep{width:240px;height:1px;background:#666}
  .field{width:244px;height:21px;background:var(--field);border:1px solid #bbb;font-family:Georgia,serif;font-style:italic;font-size:10px;color:#777;padding:3px 11px}
  .social{display:flex;gap:14px;font-size:11px;color:#fff}
  .social span{display:flex;align-items:center;gap:5px}
  .social i{display:inline-block;width:12px;height:12px;background:var(--accent)}
  .footer-links{font-size:10px;line-height:21.5px;color:var(--footer-text)}
  .copyright{font-size:10px;color:#fff}
</style>
</head>
<body>

<div class="abs topbar"></div>
<nav class="abs util-nav"><span>admin</span><span>device</span><span>settings</span><span>signout</span></nav>
<div class="abs search">Site Search..
  <svg width="32" height="32" viewBox="0 0 32 32" aria-hidden="true"><circle cx="13" cy="13" r="8" fill="#dfe9ef" stroke="#fff" stroke-width="2"/><line x1="19" y1="19" x2="27" y2="27" stroke="#c9d3d9" stroke-width="4" stroke-linecap="round"/></svg>
</div>

<header class="abs header">
  <div class="abs brand">BrisketLoom</div>
  <nav class="abs main-nav"><span class="current">Home</span><span>About Me</span><span>Latest News</span><span>Services</span><span>Contact Us</span></nav>
</header>

<h1 class="abs hero-title">Lost Your Phone?</h1>
<div class="abs features">
  <div class="feature" style="left:164px;top:0"><svg width="33" height="33" viewBox="0 0 33 33" aria-hidden="true"><circle cx="16.5" cy="16.5" r="15" fill="#8cc3e1"/><circle cx="16.5" cy="16.5" r="10" fill="#fff"/><circle cx="16.5" cy="16.5" r="6" fill="var(--accent)"/></svg>Wipe data</div>
  <div class="feature" style="left:393px;top:0"><svg width="33" height="33" viewBox="0 0 33 33" aria-hidden="true"><circle cx="16.5" cy="16.5" r="15" fill="#8cc3e1"/><circle cx="16.5" cy="16.5" r="10" fill="#fff"/><circle cx="16.5" cy="16.5" r="6" fill="var(--accent)"/></svg>Lock it</div>
  <div class="feature" style="left:584px;top:0"><svg width="33" height="33" viewBox="0 0 33 33" aria-hidden="true"><circle cx="16.5" cy="16.5" r="15" fill="#8cc3e1"/><circle cx="16.5" cy="16.5" r="10" fill="#fff"/><circle cx="16.5" cy="16.5" r="6" fill="var(--accent)"/></svg>Ring it</div>
  <div class="feature" style="left:774px;top:0"><svg width="33" height="33" viewBox="0 0 33 33" aria-hidden="true"><circle cx="16.5" cy="16.5" r="15" fill="#8cc3e1"/><circle cx="16.5" cy="16.5" r="10" fill="#fff"/><circle cx="16.5" cy="16.5" r="6" fill="var(--accent)"/></svg>Find it</div>
</div>
<div class="abs rule" style="left:314px;top:353px;width:465px"></div>

<div class="abs cta">
  <svg width="62" height="62" viewBox="0 0 62 62" aria-hidden="true"><circle cx="31" cy="31" r="30" fill="#555"/><circle cx="31" cy="31" r="27" fill="none" stroke="#888" stroke-width="2"/><path d="M8 24h22V12l22 19-22 19V38H8z" fill="#fff"/></svg>
  <span>Get Me App</span>
</div>
<div class="abs rule" style="left:90px;top:481px;width:873px"></div>

<section>
  <h2 class="abs section-title" style="left:92px;top:528px">Services</h2>
  <p class="abs body-copy" style="left:92px;top:572px;width:260px">Lorem ipsum dolor sit amet, consectetur adipisicing elit, sed do eiusmod tempor incididunt ut labore et dolore magna aliqua. Ut enim ad minim veniam, quis nostrud exercitation ullamco laboris nisi ut aliquip ex ea commodo consequat</p>

  <div class="abs photo" role="img" aria-label="Businessman talking on a mobile phone in an office" style="left:381px;top:510px;width:279px;height:144px;background:linear-gradient(90deg,#e8eef0 0%,#c9d6dc 45%,#7d8fa3 75%,#2e3e5c 100%)"></div>
  <h3 class="abs card-title" style="left:381px;top:670px">Lost Or Stolen Phones?</h3>
  <p class="abs body-copy" style="left:381px;top:695px;width:280px">Lorem ipsum dolor sit amet, consectetur adipisicing elit, sed do eiusmod tempor incididunt ut labore et dolore.</p>

  <div class="abs photo" role="img" aria-label="Mobile phone wrapped in a chain with a padlock" style="left:694px;top:510px;width:280px;height:144px;background:radial-gradient(ellipse at 55% 50%,#6b6660 0%,#2a2826 45%,#050505 80%)"></div>
  <h3 class="abs card-title" style="left:695px;top:670px">Protect and Secure</h3>
  <p class="abs body-copy" style="left:695px;top:695px;width:280px">Lorem ipsum dolor sit amet, consectetur adipisicing elit, sed do eiusmod tempor incididunt ut labore et dolore.</p>
</section>
<div class="abs rule" style="left:90px;top:749px;width:873px"></div>

<section>
  <h2 class="abs section-title" style="left:96px;top:776px">Latest News</h2>
  <article class="abs news-item" style="left:117px;top:819px;width:229px">
    <div class="news-title"><svg width="15" height="15" viewBox="0 0 15 15" aria-hidden="true"><circle cx="7.5" cy="7.5" r="7.5" fill="var(--accent)"/><path d="M4 7.8l2.4 2.4L11 5.3" stroke="#fff" stroke-width="2" fill="none"/></svg>Lorem ipsum dolor sit amet</div>
    <p class="body-copy">Lorem ipsum dolor sit amet, consectetur adipisicing elit, sed do eiusmod tempor incididunt ut labore et dolore magna aliqua. Ut enim ad minim veniam, quis nostrud exercitation ullamco laboris nisi ut aliquip ex ea commodo consequat</p>
  </article>
  <article class="abs news-item" style="left:422px;top:819px;width:229px">
    <div class="news-title"><svg width="15" height="15" viewBox="0 0 15 15" aria-hidden="true"><circle cx="7.5" cy="7.5" r="7.5" fill="var(--accent)"/><path d="M4 7.8l2.4 2.4L11 5.3" stroke="#fff" stroke-width="2" fill="none"/></svg>Lorem ipsum dolor sit amet</div>
    <p class="body-copy">Lorem ipsum dolor sit amet, consectetur adipisicing elit, sed do eiusmod tempor incididunt ut labore et dolore magna aliqua. Ut enim ad minim veniam, quis nostrud exercitation ullamco laboris nisi ut aliquip ex ea commodo consequat</p>
  </article>
  <article class="abs news-item" style="left:726px;top:819px;width:229px">
    <div class="news-title"><svg width="15" height="15" viewBox="0 0 15 15" aria-hidden="true"><circle cx="7.5" cy="7.5" r="7.5" fill="var(--accent)"/><path d="M4 7.8l2.4 2.4L11 5.3" stroke="#fff" stroke-width="2" fill="none"/></svg>Lorem ipsum dolor sit amet</div>
    <p class="body-copy">Lorem ipsum dolor sit amet, consectetur adipisicing elit, sed do eiusmod tempor incididunt ut labore et dolore magna aliqua. Ut enim ad minim veniam, quis nostrud exercitation ullamco laboris nisi ut aliquip ex ea commodo consequat</p>
  </article>
</section>

<footer class="abs footer">
  <div class="abs footer-head" style="left:85px;top:25px">OUR BLOG</div>
  <div class="abs btn" style="left:247px;top:17px;width:75px;height:22px;line-height:20px">FOLLOW US &gt;&gt;</div>
  <p class="abs blog-copy" style="left:85px;top:62px">Lorem ipsum dolor sit amet, consectetur adipisicing elit, sed do eiusmod tempor incididunt ut labore et dolore magna aliqua.</p>
  <div class="abs blog-sep" style="left:85px;top:105px"></div>
  <p class="abs blog-copy" style="left:85px;top:119px">Lorem ipsum dolor sit amet, consectetur adipisicing elit, sed do eiusmod tempor incididunt ut labore et dolore magna aliqua.</p>
  <div class="abs blog-sep" style="left:85px;top:162px"></div>
  <p class="abs blog-copy" style="left:85px;top:175px">Lorem ipsum dolor sit amet, consectetur adipisicing elit, sed do eiusmod tempor incididunt ut labore et dolore magna aliqua.</p>

  <div class="abs footer-head" style="left:428px;top:18px">QUICK CONTACT</div>
  <div class="abs field" style="left:430px;top:46px">Name</div>
  <div class="abs field" style="left:430px;top:72px">Phone</div>
  <div class="abs field" style="left:430px;top:99px">E-mail</div>
  <div class="abs btn" style="left:581px;top:126px;width:89px;height:28px;line-height:26px;font-size:11px">SUBMIT&gt;&gt;</div>

  <div class="abs footer-head" style="left:432px;top:181px;font-size:11px">FOLLOW US</div>
  <div class="abs social" style="left:515px;top:182px"><span><i></i>Orbit</span><span><i></i>Relay</span><span><i></i>Pulse</span></div>

  <ul class="abs footer-links" style="left:821px;top:19px;list-style:none">
    <li>Terms and Conditions</li><li>Privacy Policy</li><li>Frequently Asked Questions</li><li>About Us</li><li>Our Services</li><li>Contact Us</li>
  </ul>
  <div class="abs copyright" style="left:710px;top:183px">Copyright © 2012. BrisketLoom inc All rights reserved</div>
</footer>

</body>
</html>
```